Consulting company business cards

We have a base design, but would be willing to update. We have a new logo/"tag" that needs to be added. Current business card design is attached for reference into our "style."

Industry/Entity Type

Business

Contact Information for Business Card

Should contain name and title, office number, mobile number if appropriate, e-mail, website, physical address, and company logo.

Font styles to use
Other font styles liked:
• See current card design on KorvandBCard

Colors
0455a3
85acd3
aaaaaa

Requirements
Must have
• Our colors are navy blue, gray, and a lighter blue
Nice to have
• Design that I can easily drop in new names/titles as we hire employees.

```html
<!DOCTYPE html>
<html lang="en">
<head>
<meta charset="utf-8">
<title>Teravale Business Card</title>
<link rel="stylesheet" href="https://fonts.googleapis.com/css2?family=Source+Sans+3:wght@400;600;700&display=swap">
<style>
  :root {
    --page-bg: #e6e8eb;
    --card-top: #eef1f4;
    --card-top-edge: #dfe4e9;
    --navy-deep: #0c1826;
    --navy: #1a2e44;
    --brand-navy: #1d2b3a;
    --light-blue: #85acd3;
    --swoosh-blue: #4f7ea8;
    --gray: #aaaaaa;
    --text-soft: #c6ccd3;
    --text-warm: #cbbd99;
    --white: #f4f6f8;
  }
  * { box-sizing: border-box; margin: 0; padding: 0; }
  html, body {
    width: 1200px;
    height: 969px;
    overflow: hidden;
    background: var(--page-bg);
    font-family: "Source Sans 3", "Myriad Pro", Arial, sans-serif;
  }
  .business-card {
    position: absolute;
    left: 150px;
    top: 228px;
    width: 900px;
    height: 512px;
    border-radius: 30px;
    overflow: hidden;
    background: linear-gradient(180deg, var(--card-top) 0%, var(--card-top-edge) 50%);
    box-shadow: 0 18px 40px rgba(20, 30, 45, 0.18);
  }
  .card-shapes {
    position: absolute;
    inset: 0;
    width: 900px;
    height: 512px;
  }
  .brand {
    position: absolute;
    top: 62px;
    left: 0;
    width: 100%;
    text-align: center;
  }
  .brand-line {
    display: inline-flex;
    align-items: center;
    gap: 22px;
  }
  .brand-name {
    font-size: 92px;
    font-weight: 700;
    letter-spacing: 4px;
    line-height: 1;
    color: var(--brand-navy);
  }
  .brand-dot {
    width: 58px;
    height: 58px;
    border-radius: 50%;
    background: var(--brand-navy);
  }
  .tagline {
    margin-top: 12px;
    font-size: 22px;
    font-weight: 400;
    letter-spacing: 3px;
    color: var(--brand-navy);
  }
  .person {
    position: absolute;
    top: 318px;
    right: 492px;
    text-align: right;
    line-height: 1.3;
  }
  .person-name {
    font-size: 29px;
    font-weight: 600;
    letter-spacing: 0.5px;
    color: var(--light-blue);
  }
  .person-title {
    font-size: 23px;
    color: var(--white);
    margin-bottom: 8px;
  }
  .person-address {
    font-size: 22px;
    color: var(--text-soft);
    line-height: 1.45;
  }
  .divider {
    position: absolute;
    left: 437px;
    top: 322px;
    width: 1px;
    height: 146px;
    background: rgba(170, 170, 170, 0.45);
  }
  .contact {
    position: absolute;
    top: 322px;
    left: 463px;
    font-size: 22px;
    line-height: 1.5;
  }
  .contact-phone { color: var(--text-warm); }
  .contact-email, .contact-web { color: var(--text-soft); }
</style>
</head>
<body>
  <section class="business-card" aria-label="Teravale business card">
    <svg class="card-shapes" viewBox="0 0 900 512" aria-hidden="true">
      <defs>
        <linearGradient id="bandFill" x1="0" y1="0" x2="0" y2="1">
          <stop offset="0" stop-color="#1a2e44"/>
          <stop offset="1" stop-color="#0c1826"/>
        </linearGradient>
      </defs>
      <path d="M0 232 C 180 268, 430 262, 600 238 C 720 222, 820 222, 900 236 L 900 512 L 0 512 Z" fill="url(#bandFill)"/>
      <path d="M0 200 C 150 232, 330 232, 520 212 C 680 196, 800 194, 900 214 L 900 232 C 800 214, 690 214, 560 228 C 380 248, 170 250, 0 214 Z" fill="var(--swoosh-blue)" opacity="0.85"/>
      <path d="M0 214 C 170 250, 380 248, 560 228 C 690 214, 800 214, 900 232 L 900 236 C 820 222, 720 222, 600 238 C 430 262, 180 268, 0 232 Z" fill="#f4f6f8" opacity="0.9"/>
    </svg>

    <div class="brand">
      <div class="brand-line">
        <span class="brand-name">TERAVALE</span>
        <span class="brand-dot"></span>
      </div>
      <p class="tagline">A CLOUD CONSULTING COMPANY</p>
    </div>

    <div class="person">
      <p class="person-name">DANAKORVAND</p>
      <p class="person-title">Office Manager</p>
      <p class="person-address">1850 W 48th ST<br>Fairview Indiana 46010</p>
    </div>

    <div class="divider"></div>

    <div class="contact">
      <p class="contact-phone">555.204.1830 (O)</p>
      <p class="contact-phone">555.204.1871(F)</p>
      <p class="contact-email">dkorvand@teravaletech.com</p>
      <p class="contact-web">www.teravaletech.com</p>
    </div>
  </section>
</body>
</html>
```